New Business Card Design for Manufacturing

We are an engineering/manufacturing company that offers Advanced machining/assembly/engineering services, as well as innovative products for the heavy duty engine cooling markets.

We are looking to get a new business card designed that is clean and modern looking, but still fits the wide range of technical/skilled work we do.

- We hope to use this design as the base for other design work in new Presentations, web, and print work.

Industry/Entity Type

Engineering

Contact Information for Business Card

Our preferred color of blue is (RGB) 22/71/159 but can vary slightly from that color. Our content will be our Logo and full company name (Vantrell Forge Works, Inc.), company address, name, job title, phone number with extension, cell number, fax number, website, and email address on the cards.
We'd like the full company name next to the logo, but we are open to other interpretations of that layout.
Preferably, we would like the back side to be clean with just our logo, and the front to contain all of the contact information.

Colors
2f74b4
0355a3
85abd2

Requirements
Must have
• - Logo, company name, needed content - We are open to interpretation beyond that.
• - Standard size business card.
• - Horizontal orientation.
• - Enough space for lengthy names / job titles (for example, a job title could read "Directory of Human Resources" or "V.P. of Governmental Affairs"). We need this to look clean, whether the title be short (CEO) or long (as described above).

```html
<!DOCTYPE html>
<html lang="en">
<head>
<meta charset="utf-8">
<title>Vantrell Forge Works – Business Card</title>
<link rel="stylesheet" href="https://fonts.googleapis.com/css2?family=Open+Sans:wght@400;600;700;800&family=Merriweather+Sans:wght@500&display=swap">
<style>
  :root {
    --backdrop: #e4e2de;
    --card-light: #f3f2ef;
    --brand-blue: #16479f;
    --band-blue: #1d5598;
    --band-deep: #15457f;
    --name-tone: #eadfcd;
    --contact-tone: #f1ece4;
    --muted-tone: #d9e2ee;
    --tagline: #6d7178;
  }
  * { margin: 0; padding: 0; box-sizing: border-box; }
  html, body {
    width: 1200px; height: 1047px; overflow: hidden;
    background: var(--backdrop);
    font-family: "Open Sans", Arial, sans-serif;
  }
  .business-card {
    position: absolute; left: 120px; top: 236px;
    width: 960px; height: 575px;
    background: var(--card-light);
    box-shadow: 0 18px 40px rgba(0,0,0,.18);
    overflow: hidden;
  }
  .card-band { position: absolute; inset: 0; }
  .brand-lockup {
    position: absolute; left: 0; right: 0; top: 62px;
    text-align: center;
  }
  .brand-name {
    font-weight: 800; font-size: 52px; letter-spacing: .5px;
    color: var(--brand-blue); line-height: 1.1;
  }
  .brand-tagline {
    margin-top: 14px;
    font-weight: 700; font-size: 21px; letter-spacing: 1.5px;
    text-transform: uppercase; color: var(--tagline);
  }
  .contact-list {
    position: absolute; left: 52px; top: 398px;
    list-style: none;
  }
  .contact-item {
    display: flex; align-items: center;
    height: 34.5px; font-size: 23px; color: var(--contact-tone);
  }
  .contact-icon { width: 22px; height: 22px; margin-right: 20px; fill: var(--muted-tone); }
  .person-block {
    position: absolute; right: 51px; top: 316px; text-align: right;
  }
  .person-name {
    font-family: "Merriweather Sans", "Open Sans", sans-serif;
    font-weight: 500; font-size: 36px; color: var(--name-tone); line-height: 1.2;
  }
  .person-title { font-size: 22px; color: var(--muted-tone); margin-top: 4px; }
  .office-details {
    position: absolute; right: 51px; top: 432px; text-align: right;
    font-size: 23px; color: var(--name-tone); line-height: 34.5px;
  }
</style>
</head>
<body>
  <div class="business-card">
    <svg class="card-band" width="960" height="575" viewBox="0 0 960 575" aria-hidden="true">
      <defs>
        <linearGradient id="bandShade" x1="0" y1="0" x2="0" y2="1">
          <stop offset="0" stop-color="var(--band-blue)"/>
          <stop offset="1" stop-color="var(--band-deep)"/>
        </linearGradient>
      </defs>
      <path d="M0 170 Q480 340 960 164 L960 575 L0 575 Z" fill="url(#bandShade)"/>
    </svg>

    <div class="brand-lockup">
      <div class="brand-name">Vantrell Forge Works</div>
      <div class="brand-tagline">Precision in Every Part</div>
    </div>

    <ul class="contact-list">
      <li class="contact-item">
        <svg class="contact-icon" viewBox="0 0 24 24"><path d="M3 9c0-3 4-5 9-5s9 2 9 5v2h-5V9c-1-.6-2.4-1-4-1s-3 .4-4 1v2H3zM6 12h12l2 8H4z"/></svg>
        555-0142-2210 (ext. 12)
      </li>
      <li class="contact-item">
        <svg class="contact-icon" viewBox="0 0 24 24"><path d="M7 2h10a1 1 0 0 1 1 1v18a1 1 0 0 1-1 1H7a1 1 0 0 1-1-1V3a1 1 0 0 1 1-1zm1 3v12h8V5zm4 13.5a1.2 1.2 0 1 0 0 2.4 1.2 1.2 0 0 0 0-2.4z"/></svg>
        555-0188-4307
      </li>
      <li class="contact-item">
        <svg class="contact-icon" viewBox="0 0 24 24"><path d="M7 2h8l3 3v4H7zM4 10h16a1 1 0 0 1 1 1v7h-3v4H6v-4H3v-7a1 1 0 0 1 1-1zm4 7v3h8v-3z"/></svg>
        555-0163-9925
      </li>
      <li class="contact-item">
        <svg class="contact-icon" viewBox="0 0 24 24"><path d="M2 5h20v14H2zm2 2v.5l8 5.5 8-5.5V7l-8 5z"/></svg>
        m.whitfield@vantrellforge.com
      </li>
    </ul>

    <div class="person-block">
      <div class="person-name">Marcus Hale Whitfield</div>
      <div class="person-title">Managing Director</div>
    </div>

    <div class="office-details">
      <div class="office-line">418 Millrace Rd., Dalton Falls,</div>
      <div class="office-line">Brookvale, US 482190</div>
      <div class="office-line">www.vantrellforge.com</div>
    </div>
  </div>
</body>
</html>
```